Business Card Design

Looking for business card designs for a new business. there will be two cards of the same design (both lots of information below in contact info). We would like the logo diagonally across the card with the information split above and below the logo similar to sketch. happy to look at similar alternatives
Please use same colours as in logo design

Industry/Entity Type

Business

Contact Information for Business Card

Dwight Halloran
mob - 0491 738 204
ph - 02 6148 3920
fax - 02 6148 3975
email - dwight@kestrelbeams.com.au
14 Larkmoor Road, Brackley Vale NSW 2391

Colin Marchetti
mob - 0438 912 557
ph - 02 6148 3920
fax - 02 6148 3975
email - colin@kestrelbeams.com.au

```html
<!DOCTYPE html>
<html lang="en">
<head>
<meta charset="utf-8">
<title>Kestrel Beams – Business Card</title>
<link href="https://fonts.googleapis.com/css2?family=Open+Sans:wght@400;700&family=Ubuntu:wght@700&display=swap" rel="stylesheet">
<style>
  :root {
    --teal: #0b7f7a;
    --white: #ffffff;
    --ink: #111111;
    --backdrop: #ece9e4;
  }
  * { box-sizing: border-box; margin: 0; padding: 0; }
  html, body { width: 767px; height: 1200px; overflow: hidden; }
  body {
    background: var(--backdrop);
    font-family: "Open Sans", Arial, sans-serif;
    position: relative;
  }
  .card {
    position: absolute;
    background: var(--teal);
    overflow: hidden;
    box-shadow: 0 2px 6px rgba(0,0,0,0.25);
  }
  .card-front { left: 26px; top: 33px; width: 714px; height: 412px; }
  .card-back { left: 168px; top: 465px; width: 409px; height: 716px; }

  .band { position: absolute; inset: 0; width: 100%; height: 100%; }

  .holder-name {
    position: absolute; left: 14px; top: 10px;
    color: var(--white); font-weight: 700; font-size: 20px;
  }
  .wordmark {
    font-family: "Ubuntu", Arial, sans-serif;
    font-weight: 700; color: var(--ink);
    display: flex; align-items: center; gap: 12px;
    white-space: nowrap;
  }
  .wordmark-mark { width: 0.55em; height: 0.55em; background: var(--ink); flex: none; }
  .card-front .wordmark {
    position: absolute; left: 268px; top: 196px;
    font-size: 54px;
    transform: translate(-50%, -50%) rotate(-25deg);
  }
  .contact-list {
    position: absolute; right: 18px; top: 236px;
    list-style: none; text-align: right;
    color: var(--white); font-size: 16px; line-height: 27px;
  }
  .contact-list li { display: flex; justify-content: flex-end; align-items: center; gap: 6px; }
  .contact-list svg { width: 14px; height: 14px; fill: var(--white); }
  .address {
    position: absolute; right: 18px; top: 366px;
    color: var(--white); font-size: 16px;
  }

  .card-back .wordmark {
    position: absolute; left: 150px; top: 94px; height: 520px;
    writing-mode: vertical-rl;
    font-size: 68px; justify-content: center;
  }
  .web {
    position: absolute; left: 52px; top: 150px; height: 420px;
    writing-mode: vertical-rl;
    color: var(--white); font-size: 18px; letter-spacing: 2.4px;
  }
</style>
</head>
<body>
  <section class="card card-front">
    <svg class="band" viewBox="0 0 714 412" preserveAspectRatio="none" aria-hidden="true">
      <polygon points="0,198 548,0 714,0 714,34 34,412 0,412" fill="#111111"/>
      <polygon points="0,206 570,0 714,0 714,20 12,412 0,412" fill="#ffffff"/>
      <line x1="0" y1="392" x2="714" y2="8" stroke="#111111" stroke-width="4"/>
    </svg>
    <p class="holder-name">Colin Marchetti</p>
    <div class="wordmark"><span class="wordmark-mark"></span>Kestrel Beams</div>
    <ul class="contact-list">
      <li><svg viewBox="0 0 16 16"><path d="M3 1l3 3-2 2c1 2 3 4 5 5l2-2 3 3-2 3C7 15 1 9 1 3z"/></svg>02 6148 3920</li>
      <li><svg viewBox="0 0 16 16"><path d="M4 0h8v16H4zM5.5 2v10h5V2z"/></svg>0438 912 557</li>
      <li><svg viewBox="0 0 16 16"><path d="M4 1h8v5h3v9H1V6h3zM5.5 2.5v5h5v-5zM3 9v2h3V9z"/></svg>02 6148 3975</li>
      <li><svg viewBox="0 0 16 16"><path d="M1 3h14v10H1zM2.5 4.5L8 9l5.5-4.5z"/></svg>colin@kestrelbeams.com.au</li>
    </ul>
    <p class="address">14 Larkmoor Road, Brackley Vale NSW 2391</p>
  </section>

  <section class="card card-back">
    <p class="web">www.kestrelbeams.com.au</p>
    <div class="wordmark"><span class="wordmark-mark"></span>Kestrel Beams</div>
  </section>
</body>
</html>
```